Stylish Business Cards Wanted

- DOUBLE SIDED Design Required -

High end, edgy cards for a corporate and personal stylist. Must include logo,
Name: Belinda Harwick
Title: Director and Stylist
telephone : +61 8 7142 5809
email: belinda@theloombriefing.example
website: theloombriefing.example
Tag: Corporate Workwear & Uniform Specialist | Personal Stylist
Would like nice icons for telephone, email, website

Target Market(s)

Businesses wanting stylish uniforms, people wanting stylish wardrobes

Industry/Entity Type

Corporate Workwear Stylist

Contact Information for Business Card

I would like black, white and gold foiling incorporated in the design - possibly a touch of the other colours on my branding guide attached Name: Belinda Harwick Title: Director and Stylist telephone : +61 8 7142 5809 email: belinda@theloombriefing.example website: theloombriefing.example Tag: Corporate Workwear & Uniform Specialist | Personal Stylist Would like nice icons for telephone, email, website

Font styles to use
Other font styles liked:
• Raleway

Colors

Designer to choose colors to be used in the design.

Requirements
Must have
• Gold foil accents

```html
<!DOCTYPE html>
<html lang="en">
<head>
<meta charset="utf-8">
<title>The Loom Briefing – Business Cards</title>
<link href="https://fonts.googleapis.com/css2?family=Raleway:wght@400;600;700&display=swap" rel="stylesheet">
<style>
  :root {
    --backdrop: #161616;
    --card: #222222;
    --gold: #e2b43f;
    --white: #ffffff;
    --soft-white: #f2f2f2;
  }
  * { margin: 0; padding: 0; box-sizing: border-box; }
  html, body {
    width: 1200px; height: 988px; overflow: hidden;
    background: var(--backdrop);
    font-family: "Raleway", Arial, sans-serif;
  }
  .card {
    position: absolute; left: 220px;
    width: 760px; height: 434px;
    background: var(--card);
    box-shadow: 0 10px 30px rgba(0,0,0,.55);
  }
  .card--front { top: 40px; }
  .card--back { top: 514px; }

  .brand {
    position: absolute;
    display: flex; align-items: center; gap: 14px;
    color: var(--white);
    font-weight: 600;
    white-space: nowrap;
  }
  .brand__dot {
    width: 14px; height: 14px; border-radius: 50%;
    background: var(--gold);
  }
  .card--front .brand {
    left: 0; right: 0; top: 150px; justify-content: center;
    font-size: 54px; letter-spacing: 1px;
  }
  .tagline {
    position: absolute; left: 0; right: 0; top: 262px;
    text-align: center; color: var(--gold);
    font-size: 19px; font-weight: 400; letter-spacing: .3px;
  }

  .card--back .brand {
    right: 48px; top: 60px;
    font-size: 34px;
  }
  .person { position: absolute; left: 48px; top: 262px; }
  .person__name {
    color: var(--gold); font-weight: 700;
    font-size: 28px; letter-spacing: 1px; text-transform: uppercase;
  }
  .person__title { color: var(--soft-white); font-size: 17px; margin-top: 2px; }
  .divider {
    position: absolute; left: 48px; right: 48px; top: 346px;
    height: 1px; background: var(--gold);
  }
  .contacts {
    position: absolute; left: 48px; right: 48px; top: 364px;
    display: flex; justify-content: space-between; align-items: center;
    list-style: none;
    color: var(--soft-white); font-size: 15px;
  }
  .contacts__item { display: flex; align-items: center; gap: 8px; }
  .contacts__icon { width: 16px; height: 16px; flex: none; }
</style>
</head>
<body>
  <section class="card card--front" aria-label="Card front">
    <div class="brand"><span class="brand__dot"></span>The Loom Briefing</div>
    <p class="tagline">Corporate Workwear &amp; Uniform Specialist | Personal Stylist</p>
  </section>

  <section class="card card--back" aria-label="Card back">
    <div class="brand"><span class="brand__dot"></span>The Loom Briefing</div>
    <div class="person">
      <h1 class="person__name">Belinda Harwick</h1>
      <p class="person__title">Director and Stylist</p>
    </div>
    <div class="divider"></div>
    <ul class="contacts">
      <li class="contacts__item">
        <svg class="contacts__icon" viewBox="0 0 24 24" aria-hidden="true"><path fill="#e2b43f" d="M6.6 10.8a15.1 15.1 0 0 0 6.6 6.6l2.2-2.2c.3-.3.7-.4 1-.2 1.1.4 2.3.6 3.6.6.6 0 1 .4 1 1V20c0 .6-.4 1-1 1A17 17 0 0 1 3 4c0-.6.4-1 1-1h3.5c.6 0 1 .4 1 1 0 1.3.2 2.5.6 3.6.1.3 0 .7-.2 1z"/></svg>
        +61 8 7142 5809
      </li>
      <li class="contacts__item">
        <svg class="contacts__icon" viewBox="0 0 24 24" aria-hidden="true"><rect x="2" y="5" width="20" height="14" rx="1.5" fill="#e2b43f"/><path d="M3 6l9 7 9-7" fill="none" stroke="#222" stroke-width="1.8"/></svg>
        belinda@theloombriefing.example
      </li>
      <li class="contacts__item">
        <svg class="contacts__icon" viewBox="0 0 24 24" aria-hidden="true"><circle cx="12" cy="12" r="10" fill="#e2b43f"/><path d="M2 12h20M12 2c3 3 3 17 0 20M12 2c-3 3-3 17 0 20" fill="none" stroke="#222" stroke-width="1.4"/></svg>
        www.theloombriefing.example
      </li>
    </ul>
  </section>
</body>
</html>
```